Book Cover for a book on Quiet Ventures

I am self-publishing my book on Brindlecart and need a book cover made. Below are the details. See attached templates for size we need to use. I also attached a previous cover we had made that I liked. The problem with it was they were two boys helping each other but the book is about women. I'm open to your ideas on the cover though, but I wanted to show you a style I liked as an idea.
Front of Cover
Book Title: Quiet Ventures
Book Subtitle: Unvarnished Notes of a Woman Founder
Author Name: Lorna T. Pelham
Add on the Spine of Cover: Quiet Ventures and Lorna T. Pelham
Back of the Cover Text:
Quiet Ventures: Unvarnished Notes of a Woman Founder is an honest account of a business owner’s experience attempting to navigate the start-up community while also pursuing spiritual growth. Author Lorna Pelham defines a spiritual entrepreneur as “someone who runs an enterprise with the purpose of growing love rather than material gain.” This book discusses the three dimensions of Quiet Ventures:
1. The business is an integral part of the founder’s spiritual journey.
2. Employees working for the spiritual enterprise, whether they know it or not, encounter this company because it's part of their spiritual path.
3. The business itself has a life force of its own and its purpose is to further the kingdom of heaven on earth.
These three dimensions happen simultaneously and work together to produce the greatest possible result. However, this can feel confusing to a founder juggling these dimensions while also trying to manage and run a business. This is not a formulaic self-help book or roadmap. Rather, it is a compilation of personal reflections that often seem at odds with the traditional world of entrepreneurship.
Below the description add my picture (see attached for my picture)
Bio text:
Lorna Pelham founded Halvex with the vision of ushering in a life-long education system that shifts away from standardization to one that empowers people to live their purpose. In college, Lorna interned for Open Meadow, a women’s empowerment initiative where she recognized her passion for helping people find their voice. Lorna's 20-year journey has come full circle to empowering other female CEOs who are pursuing the path of Quiet Ventures.
NOTE: Please note that Brindlecart puts a bar code on the bottom right of the back cover as is noted on the attached template.
Size template is attached to the brief, here are the sizes typed out:
# Description Width (in) Height (in)
1 Full Cover 12.79 9.25
2 Front Cover 6 9
3 Safe Area 5.875 8.75
4 Bleed 0.125 0.125
5 Margin 0.125 0.125
6 Spine 0.54 9
7 Spine Safe Area 0.415 8.75
8 Spine Margin 0.062 0.062
9 Barcode Margin 0.25 0.25
Pre-publication checklist
BRINDLECART TIPS for the final cover:
1. Save as a PDF. Your cover must be a single PDF that includes the back cover, spine, and front cover as one image.
2. Flatten all transparencies. These can cause the file to print with missing or distorted content. Consult your software's documentation to learn how.
3. Embed your fonts. Consult your software's documentation to learn how.
4. Remove crop marks, color bars, template text. Crop marks are lines showing where pages should be trimmed. Color bars are strips with a series of patches used to ensure color balance during printing. Also, remove any template text, PDF creation guides, or software references.
5. Ensure your cover image meets the minimum resolution of 300 DPI (dots per inch).
6. Optimize PDFs. Optimization is useful to reduce your file size, allowing for higher performance when transferring, uploading, viewing, and printing the files.
7. Remove file security. Locked or encrypted files will fail review.
Target Market(s)
Women who want to be CEOs or are currently CEOs of companies.
Industry/Entity Type
Entrepreneurship, business, spirituality
Requirements
Must have
- Just the text on the description. A very welcoming feel.
Nice to have
- I like the idea of having a sunrise/sunset in the image somehow like in the example I attached to the brief, but again I'm open.
Should not have
- Please don't put any yoga or meditation poses or hands outstretched. I have a lot of interesting ones that look like my example so if you are going to submit after Saturday 10/29, please only do so if you have a new idea! Thanks!

```html
<!DOCTYPE html>
<html lang="en">
<head>
<meta charset="utf-8">
<title>Quiet Ventures — Full Cover Wrap</title>
<link href="https://fonts.googleapis.com/css2?family=Stint+Ultra+Condensed&family=Tinos:wght@400&display=swap" rel="stylesheet">
<style>
  :root{
    --page:#ffffff;
    --ink:#000000;
    --gold:#e6a43a;
    --gold-light:#f3c650;
    --amber:#e88e24;
    --white:#ffffff;
    --sky-top:#6e6657;
    --sky-mid:#d49a48;
    --sun:#f6b21c;
    --ridge:#1a120a;
  }
  *{margin:0;padding:0;box-sizing:border-box}
  html,body{width:1200px;height:1200px;overflow:hidden;background:var(--page)}
  .wrap{position:absolute;left:63px;top:211px;width:1074px;height:777px;background:var(--ink);color:var(--white);font-family:"Tinos",serif;overflow:hidden}

  .title-large{font-family:"Stint Ultra Condensed",serif;text-transform:uppercase;line-height:1;
    background:linear-gradient(90deg,var(--amber),var(--gold-light) 50%,var(--amber));
    -webkit-background-clip:text;background-clip:text;color:transparent;text-align:center}
  .title-small{font-family:"Stint Ultra Condensed",serif;text-transform:uppercase;color:var(--gold);
    display:flex;align-items:center;justify-content:center;gap:6px;line-height:1}
  .title-small::before,.title-small::after{content:"";height:2px;flex:1;background:linear-gradient(90deg,transparent,var(--gold))}
  .title-small::after{background:linear-gradient(90deg,var(--gold),transparent)}

  /* back cover */
  .back-title{position:absolute;left:119px;top:54px;width:300px}
  .back-title .title-large{font-size:86px;letter-spacing:3px}
  .back-title .title-small{font-size:27px;margin-top:0}
  .back-rule{position:absolute;left:69px;top:166px;width:371px;height:1px;background:linear-gradient(90deg,transparent,var(--white) 20%,var(--white) 80%,transparent)}
  .blurb{position:absolute;left:34px;top:180px;width:456px;font-size:12.6px;line-height:16.8px;text-align:justify}
  .blurb ul{list-style:none;margin:12px 0 10px 20px}
  .blurb li{position:relative;padding-left:10px;margin-bottom:8px;text-align:left}
  .blurb li::before{content:"";position:absolute;left:0;top:6px;width:4px;height:4px;border-radius:50%;background:var(--gold)}
  .author-photo{position:absolute;left:36px;top:495px;width:104px;height:118px;border:3px solid var(--amber);
    background:linear-gradient(160deg,#a9c48c,#6f9a55 55%,#d5445d)}
  .bio{position:absolute;left:154px;top:492px;width:340px;font-size:12.6px;line-height:16.8px;text-align:justify}

  /* spine */
  .spine-text{position:absolute;left:522px;top:62px;height:660px;width:56px;
    writing-mode:vertical-rl;white-space:nowrap;display:flex;align-items:center;gap:22px}
  .spine-title{font-family:"Stint Ultra Condensed",serif;text-transform:uppercase;font-size:44px;letter-spacing:2px;color:var(--gold);line-height:1}
  .spine-author{font-size:34px;color:var(--white);line-height:1}

  /* front cover */
  .front-art{position:absolute;left:588px;top:0;width:486px;height:446px;
    background:
      linear-gradient(150deg,transparent 55%,var(--ridge) 55.5%),
      radial-gradient(circle at 32% 78%,#ffd23a 0,var(--sun) 10%,#e9821e 30%,transparent 60%),
      linear-gradient(180deg,var(--sky-top),var(--sky-mid) 45%,#c86a1a 80%,var(--ridge) 100%)}
  .front-title{position:absolute;left:610px;top:448px;width:416px}
  .front-title .title-large{font-size:120px;letter-spacing:4px}
  .front-title .title-small{font-size:38px;margin-top:-2px}
  .subtitle{position:absolute;left:612px;top:614px;width:420px;text-align:center;font-size:20px;letter-spacing:7px;line-height:23px;text-transform:uppercase;white-space:nowrap}
  .subtitle::before,.subtitle::after{content:"";display:block;height:1px;margin:0 60px;background:linear-gradient(90deg,transparent,var(--gold),transparent)}
  .subtitle::before{margin-bottom:5px}
  .subtitle::after{margin-top:5px}
  .subtitle .line{display:block}
  .subtitle .accent{color:var(--gold)}
  .front-author{position:absolute;left:612px;top:694px;width:420px;text-align:center;font-size:36px;line-height:1.1}
</style>
</head>
<body>
<div class="wrap">
  <section class="back-cover">
    <div class="back-title">
      <div class="title-large">Quiet</div>
      <div class="title-small">Ventures</div>
    </div>
    <div class="back-rule"></div>
    <div class="blurb">
      <p>Quiet Ventures: Unvarnished Notes of a Woman Founder is an honest account of a business owner’s experience attempting to navigate the start-up community while also pursuing spiritual growth. Author Lorna Pelham defines a spiritual entrepreneur as “someone who runs an enterprise with the purpose of growing love rather than material gain.” This book discusses the three dimensions of Quiet Ventures:</p>
      <ul>
        <li>The business is an integral part of the founder’s spiritual journey.</li>
        <li>Employees working for the spiritual enterprise, whether they know it or not, encounter this company because it's part of their spiritual path.</li>
        <li>The business itself has a life force of its own and its purpose is to further the kingdom of heaven on earth.</li>
      </ul>
      <p>These three dimensions happen simultaneously and work together to produce the greatest possible result. However, this can feel confusing to a founder juggling these dimensions while also trying to manage and run a business. This is not a formulaic self-help book or roadmap. Rather, it is a compilation of personal reflections that often seem at odds with the traditional world of entrepreneurship.</p>
    </div>
    <div class="author-photo" role="img" aria-label="Portrait photo of the author outdoors"></div>
    <p class="bio">Lorna Pelham founded Halvex with the vision of ushering in a life-long education system that shifts away from standardization to one that empowers people to live their purpose. In college, Lorna interned for Open Meadow, a women’s empowerment initiative where she recognized her passion for helping people find their voice. Lorna's 20-year journey has come full circle to empowering other female CEOs who are pursuing the path of Quiet Ventures.</p>
  </section>

  <section class="spine">
    <div class="spine-text">
      <span class="spine-title">Quiet Ventures</span>
      <span class="spine-author">Lorna T. Pelham</span>
    </div>
  </section>

  <section class="front-cover">
    <div class="front-art" role="img" aria-label="Photo of two climbers silhouetted on a hillside against a golden sunset, one helping the other up"></div>
    <div class="front-title">
      <div class="title-large">Quiet</div>
      <div class="title-small">Ventures</div>
    </div>
    <div class="subtitle"><span class="line">Unvarnished Notes of</span><span class="line accent">A Woman Founder</span></div>
    <div class="front-author">Lorna T. Pelham</div>
  </section>
</div>
</body>
</html>
```